Brell Stone Company Business Cards

Front and Back Business Card - logo and text setup - cool design. I need workable photoshop or illustrator files so I can setup each employee card with design that is created
Updates

Hi everyone, thank you for the great entries. Please no more white and blue cards - there are so many already - black and silver only now please. thanks!

Target Market(s)

Construction Industry - Facility Managers

Industry/Entity Type

Construction

Contact Information for Business Card

I really like contemporary simplistic looks - clean neat....not opposed to seeing some black backrounds

Requirements
Must have
• Logo/website address with design on front only - www.brellstone-example.com (logo attached)
• Back:
• Name/Title/Company Address/Phone/email address
Nice to have
• Cool design
Should not have
• Nothing gimmicky like Fire or Water - since we are a Fire Protection company - it has all been done

```html
<!DOCTYPE html>
<html lang="en">
<head>
<meta charset="utf-8">
<title>Brell Stone Company Business Cards</title>
<link rel="stylesheet" href="https://fonts.googleapis.com/css2?family=Open+Sans:ital,wght@0,400;0,600;0,800;1,700&display=swap">
<style>
  :root {
    --backdrop: #1c1c1e;
    --card-black: #121214;
    --card-sheen: #26262a;
    --brand-blue: #0a2496;
    --brand-red: #ff231c;
    --fold-red: #ff5a44;
    --text-white: #ffffff;
    --text-silver: #d8d8dc;
  }
  * { margin: 0; padding: 0; box-sizing: border-box; }
  html, body { width: 1200px; height: 960px; overflow: hidden; }
  body {
    background: var(--backdrop);
    font-family: "Open Sans", Arial, sans-serif;
    position: relative;
  }
  .card {
    position: absolute;
    left: 250px;
    width: 700px;
    height: 400px;
    overflow: hidden;
    background:
      repeating-linear-gradient(90deg, rgba(255,255,255,0.018) 0 1px, transparent 1px 3px),
      linear-gradient(135deg, var(--card-sheen) 0%, var(--card-black) 55%, #0c0c0e 100%);
    box-shadow: 0 14px 40px rgba(0,0,0,0.55);
  }
  .card-front { top: 50px; }
  .card-back { top: 510px; }

  .wordmark {
    font-weight: 800;
    color: var(--brand-red);
    letter-spacing: -0.5px;
    line-height: 1;
    white-space: nowrap;
  }
  .card-front .wordmark {
    position: absolute;
    left: 0; right: 0; top: 140px;
    text-align: center;
    font-size: 50px;
  }
  .card-front .web-address {
    position: absolute;
    left: 0; right: 0; top: 232px;
    text-align: center;
    color: var(--text-silver);
    font-size: 17px;
    letter-spacing: 3px;
  }

  .card-back .wordmark {
    position: absolute;
    left: 36px; top: 96px;
    font-size: 28px;
  }
  .back-shapes { position: absolute; inset: 0; }
  .contact-block {
    position: absolute;
    right: 34px;
    top: 96px;
    text-align: right;
    color: var(--text-white);
  }
  .person-name {
    font-style: italic;
    font-weight: 700;
    font-size: 21px;
    line-height: 1.1;
  }
  .person-title {
    font-style: italic;
    font-weight: 700;
    font-size: 17px;
    line-height: 1.2;
  }
  .address {
    margin-top: 28px;
    font-size: 17px;
    line-height: 1.35;
  }
  .contact-list { list-style: none; margin-top: 16px; font-size: 17px; }
  .contact-list li {
    display: flex;
    justify-content: flex-end;
    align-items: center;
    gap: 12px;
    line-height: 1.6;
  }
  .contact-icon { width: 16px; height: 16px; flex: none; }
</style>
</head>
<body>

  <section class="card card-front" aria-label="Business card front">
    <div class="wordmark">Brell Stone Company</div>
    <div class="web-address">www.brellstone-example.com</div>
  </section>

  <section class="card card-back" aria-label="Business card back">
    <svg class="back-shapes" width="700" height="400" viewBox="0 0 700 400" aria-hidden="true">
      <polygon points="440,0 700,0 700,400 190,400" fill="var(--brand-blue)"/>
      <polygon points="400,88 450,88 450,150" fill="var(--fold-red)"/>
      <rect x="450" y="88" width="250" height="62" fill="var(--brand-red)"/>
    </svg>

    <div class="wordmark">Brell Stone Company</div>

    <div class="contact-block">
      <div class="person-name">Dana Whitfield</div>
      <div class="person-title">President</div>
      <div class="address">48 Harbor Park Road<br>Millbrook, NY 10000</div>
      <ul class="contact-list">
        <li>(555) 014-2290
          <svg class="contact-icon" viewBox="0 0 16 16" aria-hidden="true"><path d="M3.5 1.5l2.5 0 1 3.5-1.6 1.2a8 8 0 0 0 4.4 4.4l1.2-1.6 3.5 1v2.5c0 .8-.7 1.5-1.5 1.5C6.8 14 2 9.2 2 3c0-.8.7-1.5 1.5-1.5z" fill="#fff"/></svg>
        </li>
        <li>info@brellstone-example.com
          <svg class="contact-icon" viewBox="0 0 16 16" aria-hidden="true"><rect x="1.5" y="3.5" width="13" height="9" fill="none" stroke="#fff" stroke-width="1.4"/><path d="M1.5 3.5 8 9l6.5-5.5" fill="none" stroke="#fff" stroke-width="1.4"/></svg>
        </li>
        <li>www.brellstone-example.com
          <svg class="contact-icon" viewBox="0 0 16 16" aria-hidden="true"><circle cx="8" cy="8" r="6.5" fill="none" stroke="#fff" stroke-width="1.3"/><ellipse cx="8" cy="8" rx="2.8" ry="6.5" fill="none" stroke="#fff" stroke-width="1.1"/><path d="M1.5 8h13M2.6 4.7h10.8M2.6 11.3h10.8" stroke="#fff" stroke-width="1"/></svg>
        </li>
      </ul>
    </div>
  </section>

</body>
</html>
```